Need Business Card for our Real Estate Business with Sales Executive's Picture

PANTONE 484 C ( RED)

PANTONE 2766 C ( BLUE

Industry/Entity Type

Real Estate

Contact Information for Business Card

Name, Mobile, email, & picture of Person
Agency Phone, address, Web address

Requirements
Must have
• Our Logo Colours, Agent Picture,

```html
<!DOCTYPE html>
<html lang="en">
<head>
<meta charset="utf-8">
<title>Mesavale Realty – Business Card</title>
<link href="https://fonts.googleapis.com/css2?family=Open+Sans:wght@400;600&display=swap" rel="stylesheet">
<style>
  :root {
    --page-bg: #d8d5d1;
    --card-bg: #eef0f2;
    --brand-blue: #1b2a63;
    --brand-red: #9a3324;
    --band-text: #f1ece2;
    --body-text: #1f2433;
    --photo-top: #c9c2b8;
    --photo-bottom: #24305e;
  }
  * { margin: 0; padding: 0; box-sizing: border-box; }
  html, body {
    width: 1200px; height: 1054px; overflow: hidden;
    background: var(--page-bg);
    font-family: "Open Sans", Arial, sans-serif;
  }
  .card {
    position: absolute; left: 100px; top: 224px;
    width: 1000px; height: 606px;
    background: var(--card-bg);
    border-radius: 4px;
    overflow: hidden;
    box-shadow: 0 10px 30px rgba(0,0,0,0.18);
  }
  .card-band { position: absolute; left: 0; top: 0; }
  .holder-name {
    position: absolute; left: 54px; top: 94px;
    font-size: 33px; font-weight: 600; color: var(--band-text);
    line-height: 1;
  }
  .holder-title {
    position: absolute; left: 54px; top: 137px;
    font-size: 23px; font-weight: 400; color: var(--band-text);
    line-height: 1;
  }
  .brand {
    position: absolute; left: 411px; top: 222px; width: 400px;
    display: flex; align-items: center; justify-content: center; gap: 14px;
  }
  .brand-mark { width: 14px; height: 14px; background: var(--brand-red); }
  .brand-name {
    font-size: 40px; font-weight: 600; color: var(--brand-blue);
    letter-spacing: 2px; line-height: 1;
  }
  .agent-photo {
    position: absolute; left: 0; top: 242px; width: 303px; height: 364px;
    background: linear-gradient(180deg, var(--photo-top) 0%, #b9a89a 45%, var(--photo-bottom) 100%);
  }
  .office-address {
    position: absolute; left: 446px; top: 352px;
    font-size: 23px; line-height: 32px; color: var(--body-text);
  }
  .contact-list { position: absolute; left: 452px; top: 432px; list-style: none; }
  .contact-item {
    display: flex; align-items: center; height: 33px;
    font-size: 23px; color: var(--body-text);
  }
  .contact-icon { width: 20px; height: 20px; margin-right: 16px; fill: var(--brand-red); }
</style>
</head>
<body>
  <div class="card">
    <svg class="card-band" width="1000" height="210" viewBox="0 0 1000 210">
      <polygon points="0,64 1000,64 1000,201 840,201 611,184 382,201 0,201" fill="var(--brand-blue)"/>
    </svg>
    <div class="holder-name">Marissa Delgado</div>
    <div class="holder-title">Managing Director</div>

    <div class="brand">
      <span class="brand-mark"></span>
      <span class="brand-name">MESAVALE REALTY</span>
    </div>

    <div class="agent-photo" role="img" aria-label="Portrait photo of the agent in a navy suit and striped tie"></div>

    <div class="office-address">418 Juniper Ave #2210,<br>Brookfield, CO 80412</div>

    <ul class="contact-list">
      <li class="contact-item">
        <svg class="contact-icon" viewBox="0 0 20 20"><path d="M6 1h8a1.5 1.5 0 0 1 1.5 1.5v15A1.5 1.5 0 0 1 14 19H6a1.5 1.5 0 0 1-1.5-1.5v-15A1.5 1.5 0 0 1 6 1zm0.5 2.5v11h7v-11zM10 15.5a1 1 0 1 0 0 2 1 1 0 0 0 0-2z"/></svg>
        555.214.3087
      </li>
      <li class="contact-item">
        <svg class="contact-icon" viewBox="0 0 20 20"><path d="M2 7c0-2 3-4 8-4s8 2 8 4v1.5h-4V7c-1-.6-2.4-.9-4-.9s-3 .3-4 .9v1.5H2zM5 10h10l2 7H3z"/></svg>
        555-630-4419
      </li>
      <li class="contact-item">
        <svg class="contact-icon" viewBox="0 0 20 20"><path d="M2 4h16v12H2zm1.6 1.5L10 10.5l6.4-5zM3.5 14.5h13V7.3L10 12.3 3.5 7.3z"/></svg>
        mdelgado@mesavalerealty.com
      </li>
      <li class="contact-item">
        <svg class="contact-icon" viewBox="0 0 20 20"><path d="M10 2a8 8 0 1 0 0 16 8 8 0 0 0 0-16zm5.9 7h-2.6a12 12 0 0 0-1-4.6A6.5 6.5 0 0 1 15.9 9zM10 3.6c.8 1 1.6 3 1.8 5.4H8.2C8.4 6.6 9.2 4.6 10 3.6zM7.7 4.4a12 12 0 0 0-1 4.6H4.1a6.5 6.5 0 0 1 3.6-4.6zM4.1 11h2.6a12 12 0 0 0 1 4.6A6.5 6.5 0 0 1 4.1 11zm5.9 5.4c-.8-1-1.6-3-1.8-5.4h3.6c-.2 2.4-1 4.4-1.8 5.4zm2.3-.8a12 12 0 0 0 1-4.6h2.6a6.5 6.5 0 0 1-3.6 4.6z"/></svg>
        www.mesavalerealty.com
      </li>
    </ul>
  </div>
</body>
</html>
```